Verodex business card

Business card for sustainable investment company called "Verodex". Verodex is an exchange platform selling carbon credits between buyers and sellers. Carbon Credits are an environmental commodity for reducing global carbon emissions.

the card should obviously have our logo and the theme should be sustainability/environment mixed with a trading platform.

Contact Information for Business Card

Logo, Name, Title, Phone, Email

Colors
0054AA
0677BA
7BADD7
CADEEF
E8F1F8
0094D4
00A9DD
6FCCEA
C7EBF8
E9F6FB
00AB8E
00BBA5
67D7C9
C6EFE9
E9F9F6
59FF00
82FF00
B8FF75
E3FFCB
F4FFEA

```html
<!DOCTYPE html>
<html lang="en">
<head>
<meta charset="utf-8">
<title>Verodex business card</title>
<link href="https://fonts.googleapis.com/css2?family=Montserrat:wght@700&family=Poppins:wght@400;600&display=swap" rel="stylesheet">
<style>
  :root {
    --bg: #2a2a2c;
    --navy: #0f2a45;
    --ocean: #0054aa;
    --blue: #0677ba;
    --sky: #0094d4;
    --aqua: #00a9dd;
    --teal: #00ab8e;
    --mint: #00bba5;
    --lime: #82ff00;
    --leaf: #59ff00;
    --pale: #e9f9f6;
    --white: #ffffff;
    --ink: #0f2a45;
    --rule: #9aa3ad;
  }
  html, body {
    margin: 0;
    width: 1200px;
    height: 689px;
    overflow: hidden;
    background: var(--bg);
  }
  .stage {
    width: 1200px;
    height: 689px;
    display: flex;
    align-items: center;
    justify-content: center;
    gap: 40px;
  }
  .card {
    position: relative;
    width: 530px;
    height: 303px;
    border-radius: 22px;
    overflow: hidden;
  }
  /* Front */
  .front-pattern {
    position: absolute;
    inset: 0;
    background: linear-gradient(200deg, var(--ocean) 0%, var(--sky) 45%, var(--mint) 100%);
  }
  .front-brand {
    position: absolute;
    left: 50%;
    top: 50%;
    transform: translate(-50%, -50%);
    display: flex;
    align-items: center;
    gap: 14px;
    color: var(--white);
    font-family: "Montserrat", sans-serif;
    font-weight: 700;
    font-size: 44px;
    letter-spacing: 2px;
  }
  .brand-square {
    width: 34px;
    height: 34px;
    background: currentColor;
  }
  /* Back */
  .card--back { background: var(--white); }
  .back-band {
    position: absolute;
    inset: 0;
    width: 100%;
    height: 100%;
  }
  .back-brand {
    position: absolute;
    left: 38px;
    top: 118px;
    display: flex;
    align-items: center;
    gap: 10px;
    color: var(--ink);
    font-family: "Montserrat", sans-serif;
    font-weight: 700;
    font-size: 30px;
    letter-spacing: 1.5px;
  }
  .back-brand .brand-square {
    width: 24px;
    height: 24px;
    background: var(--teal);
  }
  .divider {
    position: absolute;
    left: 268px;
    top: 48px;
    width: 1px;
    height: 170px;
    background: linear-gradient(to bottom, transparent, var(--rule) 20%, var(--rule) 80%, transparent);
  }
  .contact {
    position: absolute;
    left: 290px;
    top: 54px;
    font-family: "Poppins", sans-serif;
    color: var(--ink);
  }
  .contact__name {
    margin: 0;
    font-weight: 600;
    font-size: 21px;
    letter-spacing: 0.5px;
    text-transform: uppercase;
    line-height: 1.1;
  }
  .contact__title {
    margin: 2px 0 20px;
    font-size: 13px;
    color: var(--blue);
  }
  .contact__list {
    list-style: none;
    margin: 0;
    padding: 0;
    font-size: 13px;
    line-height: 22px;
  }
  .contact__list li {
    display: flex;
    align-items: center;
    gap: 8px;
  }
  .contact__list svg {
    width: 12px;
    height: 12px;
    flex: none;
  }
  .band-mark {
    position: absolute;
    right: 36px;
    bottom: 40px;
    width: 20px;
    height: 20px;
    background: var(--lime);
  }
</style>
</head>
<body>
<main class="stage">
  <section class="card card--front">
    <div class="front-pattern" role="img" aria-label="Repeating pattern of embossed brand symbols over a blue to teal gradient"></div>
    <div class="front-brand"><span class="brand-square"></span>VERODEX</div>
  </section>

  <section class="card card--back">
    <svg class="back-band" viewBox="0 0 530 303" preserveAspectRatio="none" aria-hidden="true">
      <defs>
        <linearGradient id="stripe" x1="0" y1="0" x2="1" y2="0">
          <stop offset="0" stop-color="#0054aa"/>
          <stop offset="0.45" stop-color="#00a9dd"/>
          <stop offset="0.75" stop-color="#00bba5"/>
          <stop offset="1" stop-color="#82ff00"/>
        </linearGradient>
      </defs>
      <polygon points="0,303 0,292 530,218 530,303" fill="#0f2a45"/>
      <polygon points="0,287 0,283 530,206 530,211" fill="url(#stripe)"/>
      <polyline points="300,286 330,276 355,281 385,262 410,268 440,247 465,252 490,234"
        fill="none" stroke="#00bba5" stroke-width="1.6" stroke-linejoin="round" opacity="0.8"/>
    </svg>
    <div class="band-mark"></div>

    <div class="back-brand"><span class="brand-square"></span>VERODEX</div>
    <div class="divider"></div>

    <div class="contact">
      <h1 class="contact__name">Marcus Hale</h1>
      <p class="contact__title">Managing Director</p>
      <ul class="contact__list">
        <li>
          <svg viewBox="0 0 24 24"><path fill="#00ab8e" d="M6.6 10.8a15 15 0 0 0 6.6 6.6l2.2-2.2a1 1 0 0 1 1-.25 11.4 11.4 0 0 0 3.6.57 1 1 0 0 1 1 1V20a1 1 0 0 1-1 1A17 17 0 0 1 3 4a1 1 0 0 1 1-1h3.5a1 1 0 0 1 1 1c0 1.25.2 2.45.57 3.57a1 1 0 0 1-.25 1z"/></svg>
          044-555 210 347
        </li>
        <li>
          <svg viewBox="0 0 24 24"><path fill="#00ab8e" d="M2 5h20v14H2zm2 2v.5l8 5 8-5V7l-8 5z"/></svg>
          hello@verodexmail.com
        </li>
        <li>
          <svg viewBox="0 0 24 24"><g fill="none" stroke="#00ab8e" stroke-width="2"><circle cx="12" cy="12" r="9"/><path d="M3 12h18M12 3c3 3 3 15 0 18M12 3c-3 3-3 15 0 18"/></g></svg>
          www.verodexhub.com
        </li>
      </ul>
    </div>
  </section>
</main>
</body>
</html>
```